Corporate website design needed

We need a Contemporary Industrial/Tech/Logistics Website design to match our logistic client's business. Our client consults and build logistics solutions that they manage but they are not a typical 3PL (3rd party logistics company) which is primarily engaged in moving boxes.
PSD file only for now, home and default templates.
COMPANY CHARACTER
DESIGN LOOK AND FEEL
• The design should also be modern and visually well organized — employing a combination of visual devices and info graphics. Keep it light and not too heavy but strong/ professional. And unique.
• The design should go beyond the typical industrial pick and pack 3PL representing [Logistics Company] as a High Tech/IT logistics company.
Some examples although these are not right for this client because they have much more content and present themselves more as a 3pl.
http://www.vobrelink-hub.example/ (More right then wrong - Like this but simplified)
http://www.durmaxfreight.example (Ugly)
http://www.tpwallerton.example (More right then wrong but different focus)
http://www.pelhamrye.example/ Too 3PL trucking… We want a bit ore high level approach
The difference, the design should be a fusion in core concepts that culminate in a design which implies the following attributes. Tech (Big data / analytics / software), Consultancy (Solutions, SME, Leader), 3PL Industry vertical solutions.
NOTE: The visualization of “tech” is not “1” and “0”, but more “software and analytics” Perhaps more like www.navimetra.example.
• They need to be seen as a solutions provider in Logistics and as in Subject matter experts
TONE
The tone needs to exude professionalism, expertise, though leadership along with technical and executional excellence.
Experienced
Knowledgeable
Confident
Determined
Straightforward
WEBSITE OBJECTIVES
• Focus C-Suite executives and logistics managers’ attention on [Logistics Company]s commanding knowledge and expertise, and unique approach to supply chain solutions producing more RFP wins
• Create an easy to scan design which decreases the reliance on text through featured text, summaries, and smaller “chunked” size bits of information.
• Convey [Logistics Company] as high-tech 3PL solutions developer and services provider with a ‘high-touch’ consultative approach.
• Showcase [Logistics Company]’s value propositions. (See Slider Content)
• Showcase [Logistics Company]’s expertise in logistical analytics.
• Gain recognition as an industry leader in evolutionary new space (supply chain 2.0)
WEBSITE STRATEGY
• Reduce reliance on text (at least within initial entry points for each section)
• Typography: Watch text line lengths and readability, bolder fonts. NO SERIFS
• Generally, create a click-through format so that users who want more details can find it, and those who don’t can get a snapshot without clicking through.
• Increase visual content through info graphics and some dynamic content, photography
• Better utilize the space on each page (e.g., add visual interest, photography and iconography where appropriate to break up copy blocks and maintain readable line lengths).
COLOR SCHEME
• Create a more engaging color scheme (the logo will remain the same under all circumstances).
• Red / grayscale may work…. Not too dark or heavy. Not too much red. Ex. quiltora.example
• Also try blues and greys. They seem to like that. Open to suggestions but don’t get to crazy. Red is in their logo but too much may be a problem.
PHOTOGRAPHY
Yes. And I will upload some.
If you pick photography please be sure to note Which stock house used and the image number!
CONTENT
The content will be presented in a more hierarchical format — with lead-ins, paragraph and section headers and navigational cues to expand lengthier content allowing the visitor to more easily scan the website. No case studies, No Social media, News while on the home page should not be over emphasized. They don't post a lot so it gets dated quickly ...
I will be uploading a wire frame and other elements.
NOTE: I uploaded my EXAMPLE mock up which is close but not close enough.
I am not a great designer. So I am looking for an alternative that exceed my design ability! These examples show the basic layout but I really want some varied alternatives.
The colors are inconsistent and type not quite right. The grey bar at top is not right and should probably go away.
Please pull the basic elements in the example together into a great design.
If you have questions please contact me.
i will upload some photography tomorrow that may be of use.
Thanks!
Updates
Hi All,
We are still evaluating the submitted designs. Sorry for the delay.
Target Market(s)
This website is primarily a validation website. Few new customers will search and find them as such...
The site should be Focused on C-Suite executives and logistics managers’ attention on [Logistics Company]s commanding knowledge and expertise, and unique approach to supply chain solutions producing more RFP wins
Industry/Entity Type
Business
Font styles to use
Requirements
Must have
- Slide show, Clearly explain who they are and what they do.
Create an easy to scan design which decreases the reliance on text through featured text, summaries, and smaller “chunked” size bits of information.
Convey [Logistics Company] as high-tech 3PL solutions developer and services
provider with a ‘high-touch’ consultative approach.
Should not have
- No Ads space
No Social media
Not too cluttered. Keep it clean.

```html
<!DOCTYPE html>
<html lang="en">
<head>
<meta charset="utf-8">
<title>Corvane Logistics</title>
<link href="https://fonts.googleapis.com/css2?family=Open+Sans:wght@400;600&family=Roboto+Condensed:wght@300;700&family=Oswald:wght@400&family=PT+Serif&display=swap" rel="stylesheet">
<style>
:root{
  --red:#c8102e;
  --red-dark:#a90c25;
  --ink:#333;
  --muted:#555;
  --line:#ddd;
  --panel:#f2f2f2;
  --navy:#2b3a5c;
  --footer:#1b1b1b;
  --footer-bar:#0f0f0f;
}
*{margin:0;padding:0;box-sizing:border-box}
html,body{width:759px;height:1200px;overflow:hidden}
body{position:relative;background:#fff;font-family:Arial,Helvetica,sans-serif;color:var(--ink)}
.abs{position:absolute}
.brand{left:64px;top:20px;display:flex;align-items:center;gap:8px;font-family:'Open Sans',sans-serif;font-weight:600;font-size:15px;letter-spacing:3px;color:var(--ink)}
.brand-dot{width:22px;height:22px;border-radius:50%;background:var(--red)}
.contact-top{right:64px;top:10px;text-align:right;font-family:'Open Sans',sans-serif}
.contact-top .phone{color:var(--red);font-size:11px;display:flex;align-items:center;gap:5px;justify-content:flex-end}
.contact-top .mail{font-size:6.5px;color:#222;margin-top:1px}
.utility{left:386px;top:55px;width:309px;height:22px;background:linear-gradient(var(--red),var(--red-dark));clip-path:polygon(5px 0,100% 0,100% 100%,0 100%);display:flex;align-items:center;padding-left:46px;gap:12px;font-family:'Open Sans',sans-serif;font-size:9.5px;color:#fff}
.search{margin-left:16px;width:94px;height:15px;border-radius:8px;background:var(--red-dark);box-shadow:inset 0 1px 2px rgba(0,0,0,.3);position:relative}
.search svg{position:absolute;right:8px;top:2px}
.mainnav{left:63px;top:77px;width:632px;height:33px;background:linear-gradient(#e2e2e2,#f4f4f4);display:flex;align-items:center;font-size:9px;padding-left:12px;gap:36px}
.mainnav .on{color:var(--red)}
.hero{left:64px;top:110px;width:631px;height:218px;background:linear-gradient(90deg,#fff,#f3f3f3);box-shadow:0 2px 3px rgba(0,0,0,.3)}
.hero-art{position:absolute;left:8px;top:8px;width:272px;height:212px;background:radial-gradient(circle at 60% 42%,#c8102e 0 22%,#777 23% 38%,transparent 39%),radial-gradient(ellipse at 25% 78%,#c9a46a 0 28%,transparent 29%)}
.hero h1{position:absolute;left:354px;top:60px;font-family:'Roboto Condensed',sans-serif;font-weight:700;font-size:22px;color:#222;letter-spacing:-.3px}
.hero h1 span{color:var(--red)}
.hero h2{position:absolute;left:354px;top:83px;font-family:'Roboto Condensed',sans-serif;font-weight:300;font-size:23px;color:#444}
.hero p{position:absolute;left:358px;top:113px;width:252px;font-size:8.3px;line-height:11.3px;color:#333}
.welcome{left:64px;top:367px;width:455px}
.welcome h3{font-family:'Open Sans',sans-serif;font-weight:400;font-size:13.5px;color:#444;margin-bottom:5px}
.welcome p{font-size:8.3px;line-height:11.3px;color:#333;margin-bottom:11px}
.welcome p.tight{margin-bottom:0}
.solutions{left:540px;top:358px;width:155px;height:162px;border:1px solid #e2e2e2;border-radius:7px;padding:10px 9px}
.solutions h4{font-family:'Open Sans',sans-serif;font-weight:400;font-size:12px;color:#444;margin-bottom:5px}
.solutions li{list-style:none;display:flex;align-items:center;height:20.3px;border-bottom:1px dashed #ccc;font-family:'Open Sans',sans-serif;font-size:7.5px;color:#222;gap:6px}
.solutions li:last-child{border:0}
.solutions li b{margin-left:auto;font-weight:400;font-size:9px}
.features{left:63px;top:558px;width:632px;height:240px;background:var(--panel);border-radius:2px}
.feat{position:absolute;top:0;width:180px;text-align:center}
.feat h5{font-family:'Open Sans',sans-serif;font-weight:600;color:var(--red);font-size:11px;padding-top:14px;height:36px;border-bottom:1px solid #e0e0e0}
.feat .ph{margin:17px auto 0;width:166px;height:55px;border:2px solid #fff;box-shadow:0 0 1px #aaa}
.feat p{margin:10px auto 0;width:168px;font-size:7.8px;line-height:10.8px;text-align:justify;text-align-last:center;color:#222}
.feat a{display:block;margin-top:5px;font-size:6.5px;font-style:italic;color:var(--red);text-decoration:none}
.pager{position:absolute;left:5px;right:28px;top:223px;height:1px;background:#ddd}
.pager span{position:absolute;left:295px;top:-6px;background:var(--panel);padding:0 8px;font-size:10px;color:#666;letter-spacing:10px}
.channels{left:62px;top:834px;width:430px}
.channels h3{font-family:Arial,sans-serif;font-weight:700;font-size:13.5px;color:#555;letter-spacing:.4px}
.channels .lead{margin-top:23px;font-weight:700;font-size:8.2px;line-height:12.5px;color:#111;padding-left:3px}
.channels p{margin-top:6px;font-size:8.3px;line-height:12.4px;color:#333}
.channels .cta{margin-top:11px;font-weight:700;font-size:8.3px;color:#333;padding-left:2px}
.channels .cta span{color:var(--red)}
.result{left:534px;top:822px;width:154px;height:158px;background:var(--navy);border-radius:8px;box-shadow:0 0 0 2px #dde1ea;text-align:center;color:#fff;padding-top:36px}
.result h6{font-family:'Oswald',sans-serif;font-weight:400;font-size:9px;text-decoration:underline}
.result p{margin-top:10px;font-family:'PT Serif',sans-serif;font-size:10.5px;line-height:12.7px;padding:0 4px}
.result .mark{margin:16px auto 0;display:flex;align-items:center;justify-content:center;gap:5px;font-family:'Open Sans',sans-serif;font-size:8px;font-weight:600;letter-spacing:1px}
.result .mark i{width:10px;height:10px;border-radius:50%;background:var(--red)}
.footer{left:0;top:1020px;width:759px;height:154px;background:var(--footer);color:#eee;font-family:'Open Sans',sans-serif}
.fcol{position:absolute;top:22px}
.fcol h4{font-weight:400;font-size:13px;margin-bottom:10px}
.fcol li{list-style:none;font-size:7.5px;line-height:13.8px}
.fcol.rule{border-right:1px solid #333;padding-right:28px}
.fbrand{position:absolute;left:534px;top:50px;display:flex;align-items:center;gap:7px;font-weight:600;font-size:11px;letter-spacing:2.5px}
.fbrand i{width:18px;height:18px;border-radius:50%;background:var(--red)}
.legal{left:0;top:1174px;width:759px;height:26px;background:var(--footer-bar);color:#bbb;font-family:'Open Sans',sans-serif;font-size:7px;padding:7px 0 0 69px;word-spacing:1px}
</style>
</head>
<body>

<div class="abs brand"><span class="brand-dot"></span>CORVANE LOGISTICS</div>

<div class="abs contact-top">
  <div class="phone">
    <svg width="14" height="12" viewBox="0 0 14 12" aria-hidden="true"><path d="M1 4c0-3 12-3 12 0l-3 1-1-2H5L4 5z M3 6h8l1 5H2z" fill="#c8102e"/><circle cx="7" cy="8.5" r="1.6" fill="#fff"/></svg>
    (555)-010-274
  </div>
  <div class="mail">E-mail: hello@corvane.example</div>
</div>

<nav class="abs utility">
  <span>Company</span><span>Careers</span><span>Contact</span>
  <span class="search"><svg width="11" height="11" viewBox="0 0 11 11" aria-hidden="true"><circle cx="4.5" cy="4.5" r="3.2" fill="none" stroke="#222" stroke-width="1.3"/><path d="M7 7l3 3" stroke="#222" stroke-width="1.6"/></svg></span>
</nav>

<nav class="abs mainnav">
  <span class="on">HOME</span><span>SOLUTIONS</span><span>OUR PROCESSES</span><span>INDUSTRIES</span>
</nav>

<section class="abs hero">
  <div class="hero-art" role="img" aria-label="Globe with red continents beside stacked cardboard shipping boxes over a faint world map"></div>
  <h1>Our Manufacturing <span>Ability</span></h1>
  <h2>Our Online Products Sales</h2>
  <p>simply dummy text of the printing and typesetting industry. Lorem Ipsum has been the industry's standard dummy text ever since the 1500s, when an unknown printer took a galley of type and scrambled it to make a type specimen book. It has survived not only five centuries,</p>
</section>

<section class="abs welcome">
  <h3>Welcome to Corvane Logistics</h3>
  <p>simply dummy text of the printing and typesetting industry. Lorem Ipsum has been the industry's standard dummy text ever since the 1500s, when an unknown printer took a galley of type and scrambled it to make a type specimen book. It has survived not only five centuries,</p>
  <p class="tight">but also the leap into electronic typesetting, remaining essentially unknown printer took a galley of type and scrambled an unknown printer took a galley of type and scrambled unchanged.</p>
  <p>simply dummy text of the printing and typesetting industry. Lorem Ipsum has been the industry's standard dummy text ever since the 1500s, when an unknown printer took a galley of type and scrambled it to make a type specimen book. It has survived not only five centuries,</p>
  <p>but also the leap into electronic typesetting, remaining essentially unknown printer took a galley of type and scrambled an unknown printer took a galley of type and scrambled unchanged.</p>
</section>

<aside class="abs solutions">
  <h4>Logistics Solutions</h4>
  <ul>
    <li><svg width="9" height="8" viewBox="0 0 9 8" aria-hidden="true"><path d="M1 4l2.5 3L8 1" fill="none" stroke="#c8102e" stroke-width="1.8"/></svg>Omni Channel Distribution<b>»</b></li>
    <li><svg width="9" height="8" viewBox="0 0 9 8" aria-hidden="true"><path d="M1 4l2.5 3L8 1" fill="none" stroke="#c8102e" stroke-width="1.8"/></svg>Reverse Logistics<b>»</b></li>
    <li><svg width="9" height="8" viewBox="0 0 9 8" aria-hidden="true"><path d="M1 4l2.5 3L8 1" fill="none" stroke="#c8102e" stroke-width="1.8"/></svg>Manufacturing Support<b>»</b></li>
    <li><svg width="9" height="8" viewBox="0 0 9 8" aria-hidden="true"><path d="M1 4l2.5 3L8 1" fill="none" stroke="#c8102e" stroke-width="1.8"/></svg>Omni Channel Distribution<b>»</b></li>
    <li><svg width="9" height="8" viewBox="0 0 9 8" aria-hidden="true"><path d="M1 4l2.5 3L8 1" fill="none" stroke="#c8102e" stroke-width="1.8"/></svg>Omni Channel Distribution<b>»</b></li>
    <li><svg width="9" height="8" viewBox="0 0 9 8" aria-hidden="true"><path d="M1 4l2.5 3L8 1" fill="none" stroke="#c8102e" stroke-width="1.8"/></svg>Omni Channel Distribution<b>»</b></li>
  </ul>
</aside>

<section class="abs features">
  <div class="feat" style="left:14px">
    <h5>LOREM IPSUM</h5>
    <div class="ph" role="img" aria-label="Row of white delivery vans parked in a lot" style="background:linear-gradient(#6c7a86,#d9dde0 45%,#9aa3a9)"></div>
    <p>Accounting is the global language of business &amp; figures. All business decision making is based on sound analysis of financial statements product.</p>
    <a>More Details &nbsp;»</a>
  </div>
  <div class="feat" style="left:224px">
    <h5>LOREM IPSUM</h5>
    <div class="ph" role="img" aria-label="Private jet flying above mountains" style="background:linear-gradient(#8fb3d6,#dbe6ee 55%,#7f95a8)"></div>
    <p>Accounting is the global language of business &amp; figures. All business decision making is based on sound analysis of financial statements product.</p>
    <a>More Details &nbsp;»</a>
  </div>
  <div class="feat" style="left:434px">
    <h5>LOREM IPSUM</h5>
    <div class="ph" role="img" aria-label="Warehouse floor with stacked cardboard boxes" style="background:linear-gradient(#4a3f36,#b08a5c 60%,#d2b48a)"></div>
    <p>Accounting is the global language of business &amp; figures. All business decision making is based on sound analysis of financial statements product.</p>
    <a>More Details &nbsp;»</a>
  </div>
  <div class="pager"><span>‹›</span></div>
</section>

<section class="abs channels">
  <h3>Proven Channels for Omni-Channel Distribution</h3>
  <div class="lead">Morbi cursus justo ac elit vehicula id luctus massa aliquet. Nam rutrum tincidunt mollis.<br>Quisque laoreet turpis dapibus ipsum auctor id imperdiet</div>
  <p>Lorem ipsum dolor sit amet, consectetur adipiscing elit. Phasellus luctus fringilla neque eu porta. In hac habitasse platea dictumst. Phasellus viverra lacus semper lectus venenatis tempor. Maecenas egestas rhoncus purus ut posuere. Ut id nisi nisi, in ultrices lectus. Integer consequat neque eu porta. In hac habitasse platea dictumst. Phasellus viverra lacus semper tincidunt metus..</p>
  <div class="cta"><span>Contact Us</span> to learn how our solutions support cross-channel growth.</div>
</section>

<aside class="abs result">
  <h6>Delivering Business Results.</h6>
  <p>We engineer profitable entrepreneurial solutions for our clients.</p>
  <div class="mark"><i></i>CORVANE</div>
</aside>

<footer class="abs footer">
  <div class="fcol rule" style="left:78px">
    <h4>Quick Links</h4>
    <ul><li>Lorem ipsum dolor sit</li><li>Amet consectetuer</li><li>Adipiscing elit</li><li>Praesent vestibulum</li><li>Molestie lacus aenean</li></ul>
  </div>
  <div class="fcol rule" style="left:226px;top:26px">
    <h4>How it Works</h4>
    <ul><li>Lorem ipsum dolor sit</li><li>Amet consectetuer</li><li>Adipiscing elit</li><li>Praesent vestibulum</li><li>Molestie lacus aenean</li></ul>
  </div>
  <div class="fcol" style="left:372px;top:26px">
    <h4>Contact Us</h4>
    <ul><li>18 Harlow Row</li><li>Dunmere, DM4 2QT</li><li>Phone:+44(0)1632 960418</li><li>Email:eu@corvane.example</li></ul>
  </div>
  <div class="fbrand"><i></i>CORVANE LOGISTICS</div>
</footer>

<div class="abs legal">Home | News | About Us | Solutions | Contact Us &nbsp;&nbsp; © 2014 Logistics &nbsp;FAQ | Privacy Policy | Site Map.</div>

</body>
</html>
```